Oil and Gas Exploration and Production company needs a business card design

We need a business card design using our logo and colors in the logo. We want a mainstream design.

```html
<!DOCTYPE html>
<html lang="en">
<head>
<meta charset="utf-8">
<title>Vardane Oil &amp; Gas – Business Card</title>
<link rel="stylesheet" href="https://fonts.googleapis.com/css2?family=Ubuntu:wght@400;500;700&display=swap">
<style>
  :root {
    --gold: #cc9c36;
    --ink: #111111;
    --paper: #ffffff;
    --backdrop: #3b332d;
    --divider: #8a6a24;
  }
  * { box-sizing: border-box; margin: 0; padding: 0; }
  html, body { width: 1200px; height: 1200px; overflow: hidden; }
  body {
    background: var(--backdrop);
    font-family: "Ubuntu", sans-serif;
    display: flex;
    flex-direction: column;
    align-items: center;
    justify-content: center;
    gap: 70px;
  }
  .card {
    width: 700px;
    height: 400px;
    position: relative;
    overflow: hidden;
  }
  .card--front {
    background: var(--gold);
    display: flex;
    flex-direction: column;
    align-items: center;
    justify-content: center;
    gap: 14px;
  }
  .brand {
    display: flex;
    align-items: center;
    gap: 14px;
    font-family: "Ubuntu", sans-serif;
    font-weight: 700;
    font-size: 46px;
    color: var(--ink);
    letter-spacing: 0.5px;
  }
  .brand__dot {
    width: 30px; height: 30px;
    border-radius: 50%;
    background: var(--ink);
  }
  .card--front .web {
    font-size: 19px;
    font-weight: 500;
    color: var(--ink);
    letter-spacing: 0.5px;
  }
  .card--back { background: var(--paper); }
  .card--back .brand { position: absolute; top: 62px; left: 0; right: 0; justify-content: center; }
  .card--back .brand__dot { background: var(--gold); }
  .person {
    position: absolute; top: 136px; left: 0; right: 0;
    text-align: center;
  }
  .person__name {
    font-size: 26px; font-weight: 700; color: var(--gold); letter-spacing: 0.5px;
  }
  .person__role { font-size: 16px; color: var(--ink); margin-top: 6px; }
  .band {
    position: absolute; left: 0; right: 0; top: 218px; height: 122px;
    background: var(--gold);
    border-top: 2px solid var(--paper);
    border-bottom: 2px solid var(--paper);
    box-shadow: 0 -6px 0 -4px var(--gold), 0 6px 0 -4px var(--gold);
    outline: 2px solid var(--gold);
    outline-offset: -8px;
    display: flex; align-items: center; justify-content: center;
  }
  .band__col { flex: 1; display: flex; flex-direction: column; gap: 10px; font-size: 17px; color: var(--ink); }
  .band__col--address { align-items: flex-end; padding-right: 24px; }
  .band__col--contact { align-items: flex-start; padding-left: 24px; }
  .band__divider { width: 1px; height: 56px; background: var(--divider); }
  .line { display: flex; align-items: center; gap: 8px; }
  .icon { width: 16px; height: 16px; flex: none; }
</style>
</head>
<body>
  <section class="card card--front">
    <div class="brand"><span class="brand__dot"></span>Vardane Oil &amp; Gas</div>
    <div class="web">www.vardaneoil.com</div>
  </section>

  <section class="card card--back">
    <div class="brand"><span class="brand__dot"></span>Vardane Oil &amp; Gas</div>
    <div class="person">
      <div class="person__name">DANIEL REYES</div>
      <div class="person__role">Director | 1-555-013-2468</div>
    </div>
    <div class="band">
      <div class="band__col band__col--address">
        <div class="line">Dummy city
          <svg class="icon" viewBox="0 0 16 16"><path d="M8 1a5 5 0 0 0-5 5c0 4 5 9 5 9s5-5 5-9a5 5 0 0 0-5-5zm0 7a2 2 0 1 1 0-4 2 2 0 0 1 0 4z" fill="#111"/></svg>
        </div>
        <div class="line">Dummy Country Land</div>
      </div>
      <div class="band__divider"></div>
      <div class="band__col band__col--contact">
        <div class="line">
          <svg class="icon" viewBox="0 0 16 16"><rect x="1" y="3" width="14" height="10" fill="#111"/><path d="M1 3l7 6 7-6" fill="none" stroke="#cc9c36" stroke-width="1.2"/></svg>
          daniel@vardaneoil.com
        </div>
        <div class="line">
          <svg class="icon" viewBox="0 0 16 16" fill="none" stroke="#111" stroke-width="1.2"><circle cx="8" cy="8" r="6.5"/><ellipse cx="8" cy="8" rx="3" ry="6.5"/><path d="M1.5 8h13M2.5 4.8h11M2.5 11.2h11"/></svg>
          www.vardaneoil.com
        </div>
      </div>
    </div>
  </section>
</body>
</html>
```